Corbeck Aluminium Design Upgrade

- This is for a layout design of the home page only. No coding required.

- The design should be based around the attached HPID (home page information design) I've attached both a JPEG of this
- Information only is in RED text. Copy to go on the design in BLACK text. Some instructions are in the HPID. Please be creative!
- The design needs to be clean and spacious
- Use the logo provided. Please use the colours from the logos in the website design.
- I've attached some images to use as examples to use for home page gallery
- The product logos (Pelvane, Trimbough etc) showed in the HPV can be googled for a higher quality image if required.
- The header can be changed/altered - just needs to have all information as per logo, along with the phone number.

- Expected standard of design examples: (Please DO NOT copy these exactly – they are just examples)
http://www.halden-works.example.nz/
http://www.plinthcove.example.nz/
http://www.dusofern.example.nz/

Width of content will be 1100 pixels when implemented as a web page. Header height (without nav bar) 150-160 pixels.

The winning PSD file will have to be provided as follows…
1. Canvas size of 2000px x 2000px - 72ppi in Adobe Photoshop (CS5 compatible)
2. Width of content section is 1100px wide - centered in the canvas
3. Any button rollovers/hovers in the PSD as hidden layers.
4. All fonts used must be Google fonts (except for the header fonts).
5. You will need to supply the chosen home page plus one example page (example page as a style guide for how all other pages will look). Example page is only the header and navigational bar at the top, an empty sector in the middle with a column (180 px wide) which can be left or right aligned which means the main sector is 920 pixels wide, and then the footer at the bottom of the page.

```html
<!DOCTYPE html>
<html lang="en">
<head>
<meta charset="utf-8">
<title>Corbeck Aluminium – Home</title>
<link rel="stylesheet" href="https://fonts.googleapis.com/css2?family=Oswald:wght@400;500;700&family=Open+Sans:wght@400;600;700&family=Arimo:wght@400;700&display=swap">
<style>
  :root{
    --navy:#1f2a6e;
    --red:#d3181e;
    --yellow:#f2c200;
    --ink:#333333;
    --page:#ececec;
    --panel:#ffffff;
    --header:#2b2b2b;
    --footer:#2f2f2f;
    --footer-base:#1f1f1f;
    --line:#d6d6d6;
  }
  *{box-sizing:border-box;margin:0;padding:0}
  html,body{width:1200px;height:2400px;overflow:hidden}
  body{background:var(--page);font-family:"Arimo",Arial,sans-serif;color:var(--ink);position:relative}

  /* header */
  .site-header{position:absolute;left:0;top:0;width:1200px;height:150px;background:var(--header)}
  .brand-name{position:absolute;left:52px;top:48px;font-family:"Open Sans",sans-serif;font-weight:700;color:#fff;font-size:38px;line-height:50px;white-space:nowrap}
  .header-contact{position:absolute;left:560px;top:26px;width:300px;text-align:center;font-family:"Open Sans",sans-serif}
  .header-contact .town{color:#fff;font-size:17px}
  .header-contact .phone{color:var(--yellow);font-size:21px;font-weight:600;margin-top:4px}
  .tagline{position:absolute;left:430px;top:96px;background:var(--red);color:#fff;font-family:"Open Sans",sans-serif;font-weight:700;font-size:14px;padding:6px 14px;letter-spacing:.5px;white-space:nowrap}
  .tagline b{color:var(--yellow);font-style:italic;margin-right:8px}
  .partner{position:absolute;right:52px;top:52px;font-family:"Oswald",sans-serif;font-weight:500;font-size:32px;color:var(--red);text-transform:uppercase;letter-spacing:1px}

  /* nav */
  .main-nav{position:absolute;left:50px;top:160px;width:1100px;height:56px;background:#fff;border:1px solid var(--line);display:flex;align-items:stretch}
  .main-nav a{display:flex;align-items:center;padding:0 13px;font-family:"Open Sans",sans-serif;font-size:13px;color:var(--ink);text-decoration:none;text-transform:uppercase;border-right:1px solid var(--line);white-space:nowrap}
  .main-nav a.home{background:#f4f4f4;padding:0 18px}
  .main-nav a.quote{margin-left:auto;border-left:1px solid var(--line)}
  .main-nav a:last-child{border-right:none}

  /* main panel */
  .content{position:absolute;left:50px;top:228px;width:1100px;height:1824px;background:var(--panel)}
  .hero-title{position:absolute;left:40px;top:30px;font-family:"Oswald",sans-serif;font-weight:500;font-size:27px;color:var(--navy);letter-spacing:.5px;white-space:nowrap}
  .quote-badge{position:absolute;left:880px;top:12px;width:200px;height:200px;border-radius:50%;background:var(--red);color:#fff;font-family:"Oswald",sans-serif;font-weight:700;font-size:21px;line-height:25px;text-align:center;display:flex;align-items:center;justify-content:center;padding:0 24px;border:5px solid #fff;box-shadow:0 0 0 2px var(--red);z-index:2;text-transform:uppercase}
  .hero{position:absolute;left:12px;top:82px;width:1068px;height:470px;background:linear-gradient(180deg,#9ebfe2 0%,#d9e4ee 40%,#e9eaea 60%,#6f8d5a 100%)}
  .hero-bar{position:absolute;left:12px;top:484px;width:1068px;height:68px;background:rgba(25,25,25,.88);display:flex;align-items:center;justify-content:space-between;padding-left:24px}
  .hero-bar h2{font-family:"Oswald",sans-serif;font-weight:500;color:#fff;font-size:26px;text-transform:uppercase;letter-spacing:.5px;white-space:nowrap}
  .hero-bar .tab{height:68px;background:var(--red);color:#fff;font-family:"Oswald",sans-serif;font-weight:500;font-size:18px;display:flex;align-items:center;padding:0 22px;text-transform:uppercase;white-space:nowrap}

  .brands{position:absolute;left:12px;top:578px;width:1068px;height:110px;border:1px solid var(--line);display:flex;align-items:center;justify-content:space-around}
  .brands span{font-family:"Oswald",sans-serif;font-weight:500;font-size:22px;color:var(--ink);text-transform:uppercase}
  .brands span.accent{color:var(--red)}

  .product{position:absolute;width:345px}
  .product h3{font-family:"Oswald",sans-serif;font-weight:500;font-size:23px;color:var(--navy);text-transform:uppercase;letter-spacing:.5px}
  .product .photo{width:345px;height:200px;margin-top:12px}
  .product h4{font-family:"Arimo",sans-serif;font-weight:400;font-size:17px;color:var(--navy);margin-top:26px}
  .product p{font-size:13.5px;line-height:21px;color:#444;margin-top:12px}
  .product p + p{margin-top:22px}

  /* footer */
  .site-footer{position:absolute;left:0;top:2062px;width:1200px;height:266px;background:var(--footer);font-family:"Arimo",sans-serif;color:#cfcfcf;font-size:13.5px}
  .foot-links{position:absolute;top:50px;list-style:none;line-height:27px}
  .foot-contact{position:absolute;left:482px;top:50px;line-height:27px}
  .foot-contact h5{font-family:"Open Sans",sans-serif;font-weight:700;color:#fff;font-size:14px;text-transform:uppercase}
  .guarantee-seal{position:absolute;left:900px;top:26px;width:130px;height:130px;border-radius:50%;background:radial-gradient(circle,#e6e6e6 0%,#9a9a9a 100%);border:6px solid #4a6fa5}
  .guarantee{position:absolute;left:865px;top:172px;width:270px;text-align:center;font-size:12.5px;line-height:18px}
  .footer-base{position:absolute;left:0;top:2328px;width:1200px;height:72px;background:var(--footer-base);display:flex;align-items:center;justify-content:space-between;padding:0 56px;font-size:13px;color:#bdbdbd}
  .follow{display:flex;align-items:center;gap:12px}
  .follow i{display:block;width:30px;height:30px;border:1px solid #555;background:#2a2a2a}
</style>
</head>
<body>

<header class="site-header">
  <div class="brand-name">Corbeck Aluminium</div>
  <div class="header-contact"><div class="town">Kerrow Vale, Wellington</div><div class="phone">(04) 555 0140</div></div>
  <div class="tagline"><b>EXCELLENCE</b>IN ALUMINIUM WINDOWS &amp; DOORS</div>
  <div class="partner">Pelvane</div>
</header>

<nav class="main-nav">
  <a class="home" href="#" aria-label="Home">
    <svg width="18" height="16" viewBox="0 0 18 16"><path d="M9 1 1 8h2v7h5v-5h2v5h5V8h2z" fill="#333"/></svg>
  </a>
  <a href="#">About Us</a>
  <a href="#">Commercial</a>
  <a href="#">New Homes</a>
  <a href="#">Replacement Joinery</a>
  <a href="#">Double Glazing</a>
  <a href="#">Conservatories</a>
  <a href="#">Gallery</a>
  <a class="quote" href="#">Get a Free Quote</a>
  <a href="#">Contact Us</a>
</nav>

<main class="content">
  <h1 class="hero-title">ENSURING STYLE AND FUNCTIONALITY WITH YOUR ALUMINIUM JOINERY</h1>
  <div class="quote-badge">Get a free quote for your journey needs</div>
  <div class="hero" role="img" aria-label="Modern white townhouses with large aluminium-framed windows under a blue sky"></div>
  <div class="hero-bar"><h2>Solutions for all commercial and residential aluminium joinery</h2><div class="tab">Commercial Joinery</div></div>

  <div class="brands">
    <span class="accent">Pelvane</span>
    <span>Trimbough</span>
    <span>Warmline</span>
    <span>Wendrel</span>
    <span>Stratum Series</span>
    <span>Stratum Glassworks</span>
  </div>

  <section class="product" style="left:5px;top:728px">
    <h3>New Homes</h3>
    <div class="photo" role="img" aria-label="New home with aluminium joinery and a green lawn" style="background:linear-gradient(180deg,#a9c4df,#d8d8d0 55%,#6b8a4f)"></div>
    <h4>Building your dream home?</h4>
    <p>Complete your dream home with quality constructed, custom-made aluminium joinery products. These products provide a range of benefits, while also being affordable and adding class to your home design.</p>
    <p>We manufacture a wide range of products for the residential market, including sliding doors, French doors, bifold doors and double glazed aluminium windows.</p>
  </section>

  <section class="product" style="left:380px;top:728px">
    <h3>Commercial</h3>
    <div class="photo" role="img" aria-label="Commercial shopfront with dark aluminium window frames" style="background:linear-gradient(180deg,#5a4a3c,#8a7a66 50%,#2f2f35)"></div>
    <h4>Improve the presentation of your business</h4>
    <p>Complete your dream home with quality constructed, custom-made aluminium joinery products. These products provide a range of benefits, while also being affordable and adding class to your home design.</p>
    <p>We manufacture a wide range of products for the residential market, including sliding doors, French doors, bifold doors and double glazed aluminium windows.</p>
  </section>

  <section class="product" style="left:750px;top:728px">
    <h3>Replacement Joinery</h3>
    <div class="photo" role="img" aria-label="Apartment building with replacement aluminium balcony joinery" style="background:linear-gradient(180deg,#b7c9dc,#d6d0c6 50%,#8f8a84)"></div>
    <h4>Tired of your old windows and doors?</h4>
    <p>Complete your dream home with quality constructed, custom-made aluminium joinery products. These products provide a range of benefits, while also being affordable and adding class to your home design.</p>
    <p>We manufacture a wide range of products for the residential market, including sliding doors, French doors, bifold doors and double glazed aluminium windows.</p>
  </section>

  <section class="product" style="left:5px;top:1287px">
    <h3>Double Glazing</h3>
    <div class="photo" role="img" aria-label="Glazed conservatory roof with aluminium framing" style="background:linear-gradient(180deg,#9fb6cc,#5c6a78 55%,#b09072)"></div>
    <h4>Building your dream home?</h4>
    <p>Complete your dream home with quality constructed, custom-made aluminium joinery products. These products provide a range of benefits, while also being affordable and adding class to your home design.</p>
    <p>We manufacture a wide range of products for the residential market, including sliding doors, French doors, bifold doors and double glazed aluminium windows.</p>
  </section>

  <section class="product" style="left:380px;top:1287px">
    <h3>Conservatories</h3>
    <div class="photo" role="img" aria-label="House with an aluminium-framed conservatory and garden" style="background:linear-gradient(180deg,#c9d2d6,#a7aca5 50%,#6d7c5a)"></div>
    <h4>Improve the presentation of your business</h4>
    <p>Complete your dream home with quality constructed, custom-made aluminium joinery products. These products provide a range of benefits, while also being affordable and adding class to your home design.</p>
    <p>We manufacture a wide range of products for the residential market, including sliding doors, French doors, bifold doors and double glazed aluminium windows.</p>
  </section>
</main>

<footer class="site-footer">
  <ul class="foot-links" style="left:56px">
    <li>Home</li><li>About Us</li><li>Commercial</li><li>New Homes</li><li>Replacement Joinery</li>
  </ul>
  <ul class="foot-links" style="left:275px">
    <li>Double Glazing</li><li>Conservatories</li><li>Gallery</li><li>Get a Free Quote</li><li>Contact Us</li>
  </ul>
  <div class="foot-contact">
    <h5>Contact Details</h5>
    <div>Phone: (04) 555 0140</div>
    <div>Fax: (04) 555 0141</div>
    <div>Physical address: 18 Larkfield Cres, Kerrow Vale</div>
    <div>Postal address: PO Box 40111, Kerrow Vale</div>
  </div>
  <div class="guarantee-seal"></div>
  <p class="guarantee">We Guarantee all our work. If there is ever a problem, we will be back to provide a solution</p>
</footer>
<div class="footer-base">
  <span>© 2014 Corbeck Aluminium Ltd. All rights reserved.</span>
  <div class="follow"><span>FOLLOW US</span><i></i><i></i><i></i><i></i></div>
</div>

</body>
</html>
```